Brightfield Ventures Inc. Letterhead

Creation of attractive and eye catching letterhead for a business start-up for the construction industry. Letterhead must relate to construction, but avoid standard hammer and tools in the design.

I forgot to add some details, sorry about that. Some pertinent info: Ph: 916-555-0187 brightfieldventures.example 448 Willowmere Ave, Ste 210 Folsom, CA 95999 info@brightfieldventures.example not sure if slogan should be in there" “Connecting construction professionals to create a purpose driven industry.” must be able to be used in word. Thanks!

```html
<!DOCTYPE html>
<html lang="en">
<head>
<meta charset="utf-8">
<title>Brightfield Ventures Inc. Letterhead</title>
<link href="https://fonts.googleapis.com/css2?family=Lato:wght@400;700;900&family=Yellowtail&display=swap" rel="stylesheet">
<style>
  :root {
    --navy: #1b1f5a;
    --red: #c8202a;
    --text: #4a4a4a;
    --muted: #555a66;
    --rule: #c9c9c9;
    --paper: #ffffff;
  }
  * { margin: 0; padding: 0; box-sizing: border-box; }
  html, body { width: 894px; height: 1200px; overflow: hidden; background: var(--paper); }
  body { font-family: "Lato", Arial, sans-serif; color: var(--text); }
  .letterhead { position: relative; width: 894px; height: 1200px; background: var(--paper); }

  .brand { position: absolute; left: 66px; top: 88px; display: flex; align-items: center; gap: 10px; }
  .brand-mark { width: 16px; height: 16px; background: var(--red); }
  .brand-name { font-weight: 900; font-size: 19px; letter-spacing: 1.2px; color: var(--navy); text-transform: uppercase; }

  .contact { position: absolute; right: 64px; top: 52px; border-left: 1px solid var(--rule); padding-left: 10px;
             font-size: 13px; line-height: 19px; color: var(--muted); }
  .contact-item { display: flex; align-items: center; gap: 5px; }
  .contact-item svg { width: 10px; height: 10px; fill: none; stroke: var(--red); stroke-width: 1.6; }

  .greeting { position: absolute; left: 66px; top: 325px; font-weight: 700; font-size: 16px; color: var(--navy); }
  .body { position: absolute; left: 66px; top: 366px; width: 764px; font-size: 16.3px; line-height: 26.7px; text-align: justify; }
  .body p { margin-bottom: 19px; hyphens: auto; }

  .closing { position: absolute; left: 66px; top: 820px; font-size: 19px; color: #222; }
  .signature { position: absolute; left: 66px; top: 852px; font-family: "Yellowtail", cursive; font-size: 36px; color: var(--navy); }

  .footer-band { position: absolute; left: 0; top: 1000px; width: 894px; height: 200px; }
  .address { position: absolute; right: 64px; top: 1158px; font-size: 14.5px; color: #fff; display: flex; align-items: center; gap: 5px; }
  .address svg { width: 11px; height: 11px; fill: none; stroke: #fff; stroke-width: 1.6; }
</style>
</head>
<body>
<main class="letterhead">
  <header>
    <div class="brand">
      <span class="brand-mark"></span>
      <span class="brand-name">Brightfield Ventures Inc.</span>
    </div>
    <div class="contact">
      <div class="contact-item">
        <svg viewBox="0 0 10 10"><circle cx="5" cy="5" r="4"/><path d="M3.5 3 L4.5 5.5 L6.5 7"/></svg>
        916-555-0187
      </div>
      <div class="contact-item">
        <svg viewBox="0 0 10 10"><rect x="1" y="2.5" width="8" height="5.5"/><path d="M1 2.5 L5 6 L9 2.5"/></svg>
        info@brightfieldventures.example
      </div>
      <div class="contact-item">
        <svg viewBox="0 0 10 10"><circle cx="5" cy="5" r="4"/><path d="M1 5 H9 M5 1 C3 3.5 3 6.5 5 9 C7 6.5 7 3.5 5 1"/></svg>
        brightfieldventures.example
      </div>
    </div>
  </header>

  <p class="greeting">Dear Mr. Lorem,</p>
  <section class="body">
    <p>Lorem ipsum dolor sit amet, consectetuer adipiscing elit, sed diam nonummy nibh euismod tincidunt ut laoreet dolore magna aliquam erat volutpat. Ut wisi enim ad minim veniam, quis nostrud exerci tation ullamcorper suscipit lobortis nisl ut aliquip ex ea commodo consequat. Duis autem vel eum iriure dolor in hendiusto odio dignissim qui blandit praesent luptatum zzril delenit augue duis dolore te feugait nulla facilisi.</p>
    <p>Lorem ipsum dolor sit amet, consectetuer adipiscing elit, sed diam nonummy nibh euismod tincidunt ut laoreet dolore magna aliquam erat volutpat. Ut wisi enim ad minim veniam, quis nostrud exerci tation ullamcorper suscipit lobortis nisl ut aliquip ex ea commodo consequat. Duis autem vel eum iriure dolor in hendiusto odio dignissim qui blandit praesent luptatum zzril delenit augue duis dolore te feugait nulla facilisi.</p>
    <p>Lorem ipsum dolor sit amet, consectetuer adipiscing elit, sed diam nonummy nibh euismod tincidunt ut laoreet dolore magna aliquam erat volutpat. Ut wisi enim ad minim veniam, quis nostrud exerci tation ullamcorper suscipit lobortis nisl ut aliquip ex ea commodo consequat. Duis autem vel eum iriure dolor in hendiusto odio dignissim qui blandit praesent luptatum zzril delenit augue duis dolore te feugait nulla facilisi.</p>
  </section>

  <p class="closing">Sincerely Your,</p>
  <p class="signature">Your Name</p>

  <svg class="footer-band" viewBox="0 0 894 200" preserveAspectRatio="none">
    <path d="M0 152 Q 200 188 560 130" fill="none" stroke="var(--red)" stroke-width="4"/>
    <path d="M0 160 Q 240 192 894 70 L894 200 L0 200 Z" fill="var(--navy)"/>
  </svg>
  <p class="address">
    <svg viewBox="0 0 10 10"><circle cx="5" cy="5" r="4"/><circle cx="5" cy="4.5" r="1.4"/></svg>
    448 Willowmere Ave, Ste 210, Folsom, CA 95999
  </p>
</main>
</body>
</html>
```